NEW Modern Sleek Business Card for VR Language Startup

Our startup is using VR to lead the next wave of world language education. We need a two-sided business card that introduces the larger organization (Brightloom Language Inc) and our contact info on one side and shows the product, Glimwoorld, on the other side.

Side 1 (contact info)= Brightloom Logo and Contact info (name, title, phone, email)

Side 2 (product)= Glimworld logo, text, and website
Text= Culturally Immersive Language Learning Games
Website= www.glimworld-play.com

Target Market(s)

Education, Technology

Contact Information for Business Card

Contact info will be updated upon approval of the design. For now, put this as a placeholder.

Perry Dunmore
Founder & CEO
pdunmore@quillpost-mail.net
(555)-014-2286

Font styles to use
Other font styles liked:
• Gibson and Century Gothic are the brand fonts

Requirements
Nice to have
• I would love to see cohesion between the design and colors of the two logos. I have attached a few business card designs that I like, so you can get a feel for my preferred style.

```html
<!DOCTYPE html>
<html lang="en">
<head>
<meta charset="utf-8">
<title>Brightloom Language – Business Card</title>
<link href="https://fonts.googleapis.com/css2?family=Lato:wght@400;700&display=swap" rel="stylesheet">
<style>
  :root {
    --backdrop: #b9b9b9;
    --card-light: #ffffff;
    --card-dark: #4a4a4a;
    --ink: #222222;
    --ink-soft: #3a3a3a;
    --on-dark: #e4e4e4;
    --accent-cyan: #2fd3ec;
    --accent-violet: #6a5cf2;
    --grad-top: #d9457a;
    --grad-mid: #6a5cf2;
    --grad-bottom: #1fe6e8;
  }
  * { box-sizing: border-box; margin: 0; padding: 0; }
  html, body {
    width: 1200px; height: 802px; overflow: hidden;
    background: var(--backdrop);
    font-family: "Lato", Arial, sans-serif;
  }
  .sheet {
    position: relative; width: 1200px; height: 802px;
    display: flex; align-items: center; justify-content: center; gap: 40px;
  }
  .card {
    position: relative; width: 540px; height: 320px; overflow: hidden;
    box-shadow: 0 4px 10px rgba(0,0,0,0.35);
  }
  .card--contact { background: var(--card-light); }
  .card--product { background: var(--card-dark); }

  .contact__art {
    position: absolute; left: 0; top: 0; width: 300px; height: 200px;
    background: linear-gradient(180deg, var(--grad-top) 0%, var(--grad-mid) 50%, var(--grad-bottom) 100%);
  }

  .brand {
    position: absolute; left: 30px; top: 233px;
    display: flex; align-items: center; gap: 12px;
  }
  .brand__dot { width: 44px; height: 44px; border-radius: 50%; background: var(--accent-violet); }
  .brand__name { font-size: 26px; font-weight: 700; color: var(--ink-soft); letter-spacing: 2px; line-height: 1; }

  .person {
    position: absolute; right: 42px; top: 203px; text-align: right; color: var(--ink);
  }
  .person__name { font-size: 21px; font-weight: 700; line-height: 1.05; }
  .person__title { font-size: 15px; line-height: 1.2; }
  .person__lines { margin-top: 16px; font-size: 15px; line-height: 1.35; }
  .person__line { display: flex; justify-content: flex-end; align-items: center; gap: 6px; }
  .person__line svg { width: 13px; height: 13px; fill: var(--ink); }

  .product { position: absolute; inset: 0; text-align: center; }
  .product__mark {
    position: absolute; left: 0; right: 0; top: 168px;
    display: flex; justify-content: center; align-items: center; gap: 12px;
  }
  .product__dot { width: 30px; height: 30px; border-radius: 50%; background: var(--accent-cyan); }
  .product__name { font-size: 40px; font-weight: 400; color: #ffffff; line-height: 1; }
  .product__tagline {
    position: absolute; left: 0; right: 0; top: 220px;
    text-transform: uppercase; font-size: 16px; line-height: 20px; color: var(--on-dark);
  }
  .product__site {
    position: absolute; left: 0; right: 0; top: 274px;
    font-size: 17px; line-height: 20px; letter-spacing: 1.5px; color: var(--accent-cyan);
  }
</style>
</head>
<body>
<main class="sheet">
  <section class="card card--contact" aria-label="Contact side">
    <div class="contact__art" role="img" aria-label="Gradient illustration area in pink, violet and cyan"></div>

    <div class="brand">
      <span class="brand__dot"></span>
      <span class="brand__name">BRIGHTLOOM</span>
    </div>

    <div class="person">
      <p class="person__name">PERRY DUNMORE</p>
      <p class="person__title">Founder &amp; CEO</p>
      <div class="person__lines">
        <p class="person__line">(555)-014-2286
          <svg viewBox="0 0 16 16" aria-hidden="true"><path d="M1 6 C1 2 15 2 15 6 L12 7 L11 5 H5 L4 7 Z M3 8 H13 L14 14 H2 Z"/></svg>
        </p>
        <p class="person__line">pdunmore@quillpost-mail.net
          <svg viewBox="0 0 16 16" aria-hidden="true"><path d="M1 3 H15 V13 H1 Z M2 4 L8 9 L14 4 Z" fill-rule="evenodd"/></svg>
        </p>
      </div>
    </div>
  </section>

  <section class="card card--product" aria-label="Product side">
    <div class="product">
      <div class="product__mark">
        <span class="product__dot"></span>
        <span class="product__name">Glimworld</span>
      </div>
      <p class="product__tagline">Culturally Immersive<br>Language Learning Games</p>
      <p class="product__site">www.glimworld-play.com</p>
    </div>
  </section>
</main>
</body>
</html>
```